Wix Design for a Clothing Design Web Marketing Site

We need a Wix design and content (including any images and copy) for a clothing design web storefront, Sew To Suit (or sewtosuit). Rough ideas and content can be found at http://marenvoltis.wix.com/sewtosuit.

Sew To Suit is an innovative business concept that combines fashion and entertainment. The business model allows customers to actively participate in the creation of fashion designs/concepts , visualize the garment in the customer’s body in 3D, and buy the physical garment made specially to fit the customer.
The fashion consultant will be able to create the design based on client's desires and test various possibilities (size, fabric, cut, etc..) in front of the customer, using software Drapova (the software is a key component of this business model)
(when developing the website use images from Drapova)
After the design is created, the customer can choose to order the actual piece. The garment will be made according to the created design, the customer measurements.

Target Market(s)

Primarily women from 25 to 45, who are fashion enthusiasts and appreciate fit and exclusivity. They are hedonistic shoppers, who shop for entertainment.
Men (metrosexuals) who are fashion enthusiasts, also hedonistic shoppers.

Industry/Entity Type

Clothing

Font styles to use
Serif
Sans Serif

Requirements
Must have
• Must have a landing page (home) or section, that gives the consumer an idea of what Sew To Suit will do for them, an about page or section that tells about the company and product, a how it works page or section that describes how it works (http://marenvoltis.wix.com/sewtosuit#!services3/c192y), and page or section about pricing, and a page or section on how to contact us.
Nice to have
• Very modern and clean. The website must be based on the main picture of the studio in the example. If that studio is the store, what will the website look like?
• Colors yellow, grey and white. Use the zig zag in yellow and white. You can change the size of the lines. The zig zagi gives the modern and bold accent. Outfits in pictures must show nicely tailored garments.

```html
<!DOCTYPE html>
<html lang="en">
<head>
<meta charset="utf-8">
<title>Sew To Suit — Storefront</title>
<link href="https://fonts.googleapis.com/css2?family=Raleway:wght@400;500;600;700&family=Roboto:wght@400;500;700&family=Roboto+Slab:wght@700&family=Oswald:wght@400;500&family=Arimo:wght@400;700&display=swap" rel="stylesheet">
<style>
:root{
  --yellow:#f0e417;
  --yellow-pale:#faf5b0;
  --ink:#1d1d1d;
  --nav:#3a3a3a;
  --line:#d9d9d9;
  --hero:#ececec;
  --footer:#050505;
  --footer-text:#b9b9b9;
  --social:#3c3c3c;
  --white:#ffffff;
  --purple:#5b3f7a;
}
*{box-sizing:border-box;margin:0;padding:0}
html,body{width:1200px;height:2305px;overflow:hidden;background:var(--white)}
body{position:relative;font-family:"Arimo",Arial,sans-serif;color:var(--ink)}
.abs{position:absolute}

/* header */
.site-header{position:absolute;left:0;top:0;width:1200px;height:149px;
  background:linear-gradient(180deg,var(--yellow-pale),#fdf9d0 55%,var(--yellow-pale))}
.brand{left:100px;top:101px;width:172px;height:32px;background:var(--yellow);
  font:700 20px/32px "Arimo",Arial,sans-serif;text-align:center;color:var(--ink)}
.account-links{right:102px;top:8px;font:400 14px/16px "Arimo",Arial,sans-serif;display:flex;gap:18px}
.shipping-note{left:487px;top:124px;font:400 14px/16px "Arimo",Arial,sans-serif;letter-spacing:.3px}
.cart-icon{left:912px;top:100px}
.cart-label{left:968px;top:103px;font:700 13px/15px "Arimo",Arial,sans-serif}
.cart-total{left:968px;top:119px;font:700 18px/20px "Arimo",Arial,sans-serif}

.main-nav{position:absolute;left:0;top:149px;width:1200px;height:55px;background:var(--nav)}
.main-nav a{position:absolute;top:12px;height:31px;font:400 14px/31px "Arimo",Arial,sans-serif;color:var(--white);text-decoration:none}
.main-nav a.active{background:var(--yellow);color:var(--ink);padding:0 16px}

/* hero */
.hero{position:absolute;left:0;top:204px;width:1200px;height:481px;
  background:radial-gradient(ellipse at 70% 40%,#f6f6f6,var(--hero) 70%)}
.hero-photo{left:92px;top:0;width:492px;height:481px;
  background:
    radial-gradient(ellipse 90px 200px at 28% 40%,rgba(250,250,250,.9),transparent 70%),
    radial-gradient(ellipse 90px 200px at 70% 40%,rgba(250,250,250,.9),transparent 70%),
    linear-gradient(180deg,#ececec 0%,#f1ebe6 35%,#efc6c8 60%,#eab9bd 100%)}
.hero-title{left:654px;top:58px;font:600 37px/48px "Raleway",sans-serif;letter-spacing:2px;color:#2b2b2b}
.hero-title em{font-style:normal;color:var(--yellow)}
.btn-shop{left:656px;top:180px;width:149px;height:49px;background:var(--yellow);
  font:700 19px/49px "Arimo",Arial,sans-serif;text-align:center;letter-spacing:1px}
.hero-bag{width:130px;height:130px;border-radius:50%;border:4px solid #fff;box-shadow:0 2px 6px rgba(0,0,0,.25);top:296px}
.dot{width:17px;height:17px;border-radius:50%;top:452px}

/* categories */
.tile{top:723px;width:323px;height:199px;display:flex;align-items:center;justify-content:center;
  font:700 17px/20px "Raleway",sans-serif;color:var(--white);text-shadow:0 1px 3px rgba(0,0,0,.7);letter-spacing:.5px}

/* trending */
.section-title{left:0;top:963px;width:1200px;text-align:center;font:400 29px/34px "Raleway",sans-serif;letter-spacing:1.5px}
.rule{height:1px;background:var(--line);top:981px}
.product{top:1035px;width:222px}
.product .photo{height:285px;position:relative}
.product .tag{position:absolute;left:11px;top:11px;background:#3d3d3d;color:#fff;font:700 12px/22px "Arimo",Arial,sans-serif;padding:0 7px;border-radius:2px}
.product .name{margin-top:16px;font:400 14px/18px "Raleway",sans-serif;letter-spacing:.4px;color:#333}
.product .stars{margin-top:6px;font-size:17px;letter-spacing:1px;color:#c9c9c9}
.product .stars b{color:#e9b20b;font-weight:400}
.product .price{margin-top:4px;font:700 16px/20px "Roboto",sans-serif}
.product .price s{font-weight:400;font-size:13px;color:#b5b5b5}
.product .actions{margin-top:8px;display:flex;gap:10px}
.btn-cart,.btn-view{height:33px;border:1px solid #cfcfcf;display:flex;align-items:center;justify-content:center;gap:5px;
  font:400 13px/1 "Arimo",Arial,sans-serif;color:#444}
.btn-cart{width:132px}.btn-view{width:32px}
.look-blue{background:radial-gradient(ellipse 70px 130px at 50% 52%,#a9c0de,#c9d6e7 60%,#eef0f3 100%)}
.look-navy{background:radial-gradient(ellipse 60px 120px at 50% 55%,#2c3f6b,#8894ad 55%,#eef0f3 100%)}
.look-grey{background:radial-gradient(ellipse 70px 120px at 50% 50%,#7c7a78,#b4b2b0 60%,#eef0f3 100%)}

/* promos */
.promo-friday{left:100px;top:1487px;width:686px;height:155px;
  background:linear-gradient(90deg,#6a6a6a,#8d8a86 50%,#6a6a6a);text-align:center;color:#fff}
.promo-friday h3{margin-top:27px;font:700 32px/35px "Roboto Slab",serif}
.promo-friday p{margin-top:6px;font:700 11px/14px "Arimo",Arial,sans-serif}
.promo-women{left:814px;top:1487px;width:286px;height:155px;background:var(--yellow);overflow:hidden}
.promo-women .model{right:0;top:0;width:132px;height:155px;
  background:radial-gradient(ellipse 50px 80px at 55% 60%,#3a3a3a,#8d8b86 60%,var(--yellow) 100%)}
.promo-women h3{position:absolute;left:17px;top:26px;font:700 24px/29px "Roboto",sans-serif;letter-spacing:1px}
.promo-women span{position:absolute;left:17px;top:124px;font:700 14px/16px "Roboto",sans-serif}

/* free shipping band */
.ship-band{left:0;top:1682px;width:1200px;height:368px;background:linear-gradient(180deg,#3b3b3b,#272727 60%,#1e1e1e)}
.ship-band h2{position:absolute;top:102px;width:1200px;text-align:center;font:700 25px/30px "Roboto",sans-serif;color:var(--yellow);letter-spacing:.8px}
.ship-band p{position:absolute;top:145px;width:1200px;text-align:center;font:400 20px/24px "Roboto",sans-serif;color:#fff}
.btn-continue{position:absolute;left:507px;top:212px;width:187px;height:51px;background:var(--yellow);
  font:400 14px/51px "Arimo",Arial,sans-serif;text-align:center}

/* footer */
.site-footer{left:0;top:2050px;width:1200px;height:255px;background:var(--footer)}
.foot-col{top:28px}
.foot-col h4{display:flex;align-items:center;gap:8px;font:400 14px/18px "Oswald",sans-serif;color:var(--yellow)}
.foot-col ul{list-style:none;margin-top:13px}
.foot-col li{font:400 13px/21.5px "Arimo",Arial,sans-serif;color:var(--footer-text)}
.social{width:42px;height:42px;border-radius:50%;top:16px;background:var(--social)}
.social-rule{height:1px;background:#444;top:37px}
.news-title{left:722px;top:86px;width:338px;text-align:center;font:400 19px/22px "Oswald",sans-serif;color:var(--yellow)}
.news-text{left:722px;top:115px;width:338px;text-align:center;font:400 13px/16px "Arimo",Arial,sans-serif;color:var(--footer-text)}
.news-input{left:722px;top:139px;width:289px;height:43px;background:#fff;font:400 13px/43px "Arimo",Arial,sans-serif;color:#999;padding-left:13px}
.news-btn{left:1011px;top:139px;width:46px;height:43px;background:var(--purple);display:flex;align-items:center;justify-content:center}
.foot-bottom{left:0;top:207px;width:1200px;height:48px;border-top:1px solid #333;font:400 13px/48px "Arimo",Arial,sans-serif;color:var(--footer-text)}
</style>
</head>
<body>

<header class="site-header" role="img" aria-label="Yellow and white zigzag header background">
  <div class="abs brand">Sew To Suit</div>
  <nav class="abs account-links">
    <span>My Account</span><span>|</span><span>My Wishlist</span><span>|</span><span>My Cart</span><span>|</span><span>Checkout</span><span>|</span><span>Log In</span>
  </nav>
  <div class="abs shipping-note">FREE SHIPPING ON ALL ORDERS, NO MINIMUM PURCHASE</div>
  <svg class="abs cart-icon" width="44" height="40" viewBox="0 0 44 40" aria-hidden="true">
    <path d="M2 4h7l5 22h24l4-16H11" fill="none" stroke="#c8201f" stroke-width="3"/>
    <rect x="13" y="12" width="27" height="12" fill="#c8201f"/>
    <circle cx="17" cy="33" r="3.5" fill="#222"/><circle cx="34" cy="33" r="3.5" fill="#222"/>
  </svg>
  <div class="abs cart-label">SHOPPING CART :</div>
  <div class="abs cart-total">item(0) - $0.00</div>
</header>

<nav class="main-nav">
  <a class="active" style="left:100px">HOME</a>
  <a style="left:215px">WHAT IS SEW TO SUIT?</a>
  <a style="left:425px">HOW IT WORKS</a>
  <a style="left:593px">PRICE</a>
  <a style="left:691px">CONTACT US</a>
</nav>

<section class="hero">
  <div class="abs hero-photo" role="img" aria-label="Two models in white tops and pink trousers holding handbags"></div>
  <h1 class="abs hero-title">ETIAM LOBOR DICTUVE<br>SALE <em>50%</em> OFF</h1>
  <div class="abs btn-shop">SHOP NOW</div>
  <div class="abs hero-bag" role="img" aria-label="Grey and orange handbag" style="left:683px;background:radial-gradient(ellipse 42px 30px at 50% 55%,#8e8a82,#c9a48e 70%,#fff 100%)"></div>
  <div class="abs hero-bag" role="img" aria-label="Brown leather handbag" style="left:823px;background:radial-gradient(ellipse 42px 30px at 50% 55%,#6a3220,#b08a78 70%,#fff 100%)"></div>
  <div class="abs hero-bag" role="img" aria-label="Orange handbag" style="left:963px;background:radial-gradient(ellipse 42px 30px at 50% 55%,#d7561e,#e8a283 70%,#fff 100%)"></div>
  <span class="abs dot" style="left:1030px;background:#3a3a3a"></span>
  <span class="abs dot" style="left:1055px;background:var(--yellow)"></span>
  <span class="abs dot" style="left:1081px;background:var(--yellow)"></span>
</section>

<section>
  <div class="abs tile" role="img" aria-label="Runway models in evening gowns" style="left:100px;background:radial-gradient(ellipse at 45% 70%,#d9d6e0,#5b5570 45%,#141320 100%)">EDITOR'S PICK</div>
  <div class="abs tile" role="img" aria-label="Row of women's shoes on a rug" style="left:439px;background:linear-gradient(180deg,#5e5b62,#8d8882 40%,#2a2a2a 65%,#e6e3de 100%)">SHOES</div>
  <div class="abs tile" role="img" aria-label="Colourful necklace and bangles" style="left:776px;background:linear-gradient(120deg,#f2d6c6,#e6b49a 35%,#d8402e 60%,#3aa0a0)">ACCESSORIES</div>
</section>

<section>
  <span class="abs rule" style="left:115px;width:340px"></span>
  <h2 class="abs section-title">TRENDING NOW</h2>
  <span class="abs rule" style="left:732px;width:345px"></span>

  <article class="abs product" style="left:111px">
    <div class="photo look-blue" role="img" aria-label="Model in light blue blazer and navy top"></div>
    <div class="name">EMBOSSED FLOWER GOWN</div>
    <div class="stars">★★★★★</div>
    <div class="price">$40.00</div>
    <div class="actions">
      <div class="btn-cart"><svg width="12" height="11" viewBox="0 0 12 11"><path d="M0 1h2l2 6h6l2-5H3" fill="none" stroke="#444" stroke-width="1.5"/><circle cx="5" cy="9.5" r="1.2" fill="#444"/><circle cx="9" cy="9.5" r="1.2" fill="#444"/></svg>ADD TO CART</div>
      <div class="btn-view"><svg width="12" height="12" viewBox="0 0 12 12"><circle cx="5" cy="5" r="3.5" fill="none" stroke="#444" stroke-width="1.6"/><path d="M7.6 7.6l3.4 3.4" stroke="#444" stroke-width="1.8"/></svg></div>
    </div>
  </article>

  <article class="abs product" style="left:364px">
    <div class="photo look-navy" role="img" aria-label="Model in navy t-shirt and black trousers"><span class="tag">SALE</span></div>
    <div class="name">EMBOSSED FLOWER GOWN</div>
    <div class="stars">★★★★★</div>
    <div class="price">$45.00 <s>$50.00</s></div>
    <div class="actions">
      <div class="btn-cart"><svg width="12" height="11" viewBox="0 0 12 11"><path d="M0 1h2l2 6h6l2-5H3" fill="none" stroke="#444" stroke-width="1.5"/><circle cx="5" cy="9.5" r="1.2" fill="#444"/><circle cx="9" cy="9.5" r="1.2" fill="#444"/></svg>ADD TO CART</div>
      <div class="btn-view"><svg width="12" height="12" viewBox="0 0 12 12"><circle cx="5" cy="5" r="3.5" fill="none" stroke="#444" stroke-width="1.6"/><path d="M7.6 7.6l3.4 3.4" stroke="#444" stroke-width="1.8"/></svg></div>
    </div>
  </article>

  <article class="abs product" style="left:619px">
    <div class="photo look-blue" role="img" aria-label="Model in light blue blazer and navy top"><span class="tag">SALE</span></div>
    <div class="name">EMBOSSED FLOWER GOWN</div>
    <div class="stars"><b>★★★★</b>★</div>
    <div class="price">$40.00 <s>$45.00</s></div>
    <div class="actions">
      <div class="btn-cart"><svg width="12" height="11" viewBox="0 0 12 11"><path d="M0 1h2l2 6h6l2-5H3" fill="none" stroke="#444" stroke-width="1.5"/><circle cx="5" cy="9.5" r="1.2" fill="#444"/><circle cx="9" cy="9.5" r="1.2" fill="#444"/></svg>ADD TO CART</div>
      <div class="btn-view"><svg width="12" height="12" viewBox="0 0 12 12"><circle cx="5" cy="5" r="3.5" fill="none" stroke="#444" stroke-width="1.6"/><path d="M7.6 7.6l3.4 3.4" stroke="#444" stroke-width="1.8"/></svg></div>
    </div>
  </article>

  <article class="abs product" style="left:872px">
    <div class="photo look-grey" role="img" aria-label="Model in grey cardigan and black skirt"><span class="tag">SALE</span></div>
    <div class="name">EMBOSSED FLOWER GOWN</div>
    <div class="stars">★★★★★</div>
    <div class="price">$48.00 <s>$60.00</s></div>
    <div class="actions">
      <div class="btn-cart"><svg width="12" height="11" viewBox="0 0 12 11"><path d="M0 1h2l2 6h6l2-5H3" fill="none" stroke="#444" stroke-width="1.5"/><circle cx="5" cy="9.5" r="1.2" fill="#444"/><circle cx="9" cy="9.5" r="1.2" fill="#444"/></svg>ADD TO CART</div>
      <div class="btn-view"><svg width="12" height="12" viewBox="0 0 12 12"><circle cx="5" cy="5" r="3.5" fill="none" stroke="#444" stroke-width="1.6"/><path d="M7.6 7.6l3.4 3.4" stroke="#444" stroke-width="1.8"/></svg></div>
    </div>
  </article>
</section>

<section>
  <div class="abs promo-friday" role="img" aria-label="Clothing flat lay behind Black Friday sale message">
    <h3>BLACK FRIDAY SALE<br>EXTRA 30% OFF SALE ITEMS</h3>
    <p>Pellentesque Pellentesque habitant morbi tristique senectus</p>
  </div>
  <div class="abs promo-women">
    <div class="abs model" role="img" aria-label="Model in black and white patterned blouse"></div>
    <h3>NEW<br>FASHION<br>FOR WOMEN</h3>
    <span>CLICK HERE ››</span>
  </div>
</section>

<section class="abs ship-band" role="img" aria-label="Dim street scene with shoppers walking">
  <h2>FREE SHIPPING ON ALL ORDERS ABOVE $200.00</h2>
  <p>You have a total of $0.00 in your cart. Use another $200.00 to get free delivery!</p>
  <div class="btn-continue">CONTINUE SHOPPING »</div>
</section>

<footer class="abs site-footer">
  <div class="abs foot-col" style="left:130px">
    <h4><svg width="14" height="14" viewBox="0 0 14 14"><path d="M1 1h6l6 6-6 6-6-6z" fill="#f0e417"/><circle cx="4" cy="4" r="1.3" fill="#050505"/></svg>SHOP</h4>
    <ul><li>Upcoming Sales</li><li>Sales Ending Soon</li><li>Clothes Out</li><li>Accessories</li></ul>
  </div>
  <div class="abs foot-col" style="left:333px">
    <h4><svg width="14" height="14" viewBox="0 0 14 14"><circle cx="7" cy="7" r="7" fill="#f0e417"/><rect x="6" y="6" width="2" height="5" fill="#050505"/><circle cx="7" cy="4" r="1.1" fill="#050505"/></svg>ACTION &amp; INFO</h4>
    <ul><li>About Us</li><li>Press</li><li>Our Partners</li><li>Gift Certificates</li></ul>
  </div>
  <div class="abs foot-col" style="left:524px">
    <h4><svg width="20" height="14" viewBox="0 0 20 14"><circle cx="7" cy="4" r="3.2" fill="#f0e417"/><circle cx="14" cy="4" r="3.2" fill="#f0e417"/><path d="M1 14c0-5 12-5 12 0zM8 14c0-5 12-5 12 0z" fill="#f0e417"/></svg>CUSTOMER CARE</h4>
    <ul><li>Help / Customer Support</li><li>Return Policy</li><li>Shipping</li><li>FAQs</li></ul>
  </div>

  <span class="abs social-rule" style="left:722px;width:36px"></span>
  <span class="abs social" style="left:762px"></span>
  <span class="abs social" style="left:816px"></span>
  <span class="abs social" style="left:870px"></span>
  <span class="abs social" style="left:922px"></span>
  <span class="abs social" style="left:977px"></span>
  <span class="abs social-rule" style="left:1024px;width:36px"></span>

  <div class="abs news-title">NEWSLETTER SIGNUP</div>
  <div class="abs news-text">Preview sales, deals, news, updates, and more</div>
  <div class="abs news-input">Enter your email address...</div>
  <div class="abs news-btn"><svg width="20" height="14" viewBox="0 0 20 14"><rect x="1" y="1" width="18" height="12" fill="none" stroke="#d8cde6" stroke-width="1.6"/><path d="M1 1l9 7 9-7" fill="none" stroke="#d8cde6" stroke-width="1.6"/></svg></div>

  <div class="abs foot-bottom">
    <span class="abs" style="left:130px">© 2013 &nbsp;Sew To Suit &nbsp;| &nbsp;LLC. All Rights Reserved.</span>
    <span class="abs" style="left:794px">Terms of us &nbsp;&nbsp;•&nbsp;&nbsp; Privacy Policy &nbsp;&nbsp;•&nbsp;&nbsp; Contact</span>
  </div>
</footer>

</body>
</html>
```